Fitness Equipment & Service

I want to make the card eye catching and fun. We are called Corvane Motion Limited and we are based in Wales. We sell, install and service all types of fitness equipment from Skipping ropes, right through the Dumbbells, Kettle bells and Barbells through to state of the art Treadmills, Running Machines and Strength Equipment. We also design and install changing room furniture and lockers.

TYPOGRAPHY
We would like to use Futrura. Futura has an appearance of efficiency and forwardness. The typeface is derived
from simple geometric forms (near-perfect circles, triangles and squares) and is based on strokes of
near-even weight, which are low in contrast. This is most visible in the almost perfectly round stroke of
the o, which is nonetheless slightly ovoid.
The lowercase has tall ascenders, which rise above the cap line. The uppercase
characters present proportions similar to those of classical Roman capitals.

TYPOGRAPHIC CONSIDERATIONS
No Strike though
No Horizontal Scaling
No Drop Shadows
No Effects
Never use less than 120% Leading

OUR CORPORATE COLOURS
BRAND GUIDELINES
We were thinking that our primary colour palette consists of the Acid Green (Pantone 382) and Process Black.

We work closely with tquarly Ltd and would like to include their name on the card somewhere. I have attached images of the other brands that we work with as an idea or the small icons I have included that illustrate what we do?. I have very kindly been given permission to use any of the images off the files that I have included below, so I hope these help. I will include these below. I would be open to suggestions if it made the card more striking Can you do it?
Updates

Hi All, Just wanted to add a few thoughts but you are the guys with the creative visions (thats why are here) We are based in Wales, UK and we would be open to lots of different ideas on a theme but must be eye catching, Bold and FUN. If you can or think that the Welsh or any dragon could be put in there then go for it (its not a must have) We have also added some ideas for colour but again its over to you!! GO FOR IT ! Thanks and look forward to your visions! Owen

Hi All, Just thought I would sen through the contact details that need to be on the card. (if you want to play around with icons instead of the wording twitter, Facebook, go for it): Corvane Motion Limited Owen Pritchard Managing Director Mob: +44 (0)7582 913 406 e-mail: sales@corvanemotion.co.uk Web: Corvanemotion.co.uk twitter: @motionLetterbin Facebook: Corvane Motion Limited

```html
<!DOCTYPE html>
<html lang="en">
<head>
<meta charset="utf-8">
<title>Corvane Motion Limited – Business Card</title>
<link rel="stylesheet" href="https://fonts.googleapis.com/css2?family=Jost:wght@400;500&display=swap">
<style>
  :root {
    --backdrop: #8c8c8c;
    --card-white: #f1f1f1;
    --navy: #0b0d3a;
    --gold: #c6952e;
    --ink: #3a3a3a;
    --ink-soft: #4a4a4a;
    --back-top: #1c62a6;
    --back-bottom: #0b1852;
    --white: #ffffff;
  }
  * { margin: 0; padding: 0; box-sizing: border-box; }
  html, body {
    width: 1105px; height: 1200px; overflow: hidden;
    background: var(--backdrop);
    font-family: "Jost", "Futura", sans-serif;
  }
  .canvas { position: relative; width: 1105px; height: 1200px; }

  .card { position: absolute; left: 182px; width: 746px; height: 426px; overflow: hidden; }

  /* Front */
  .card-front { top: 120px; background: var(--card-white); }
  .front-band { position: absolute; left: 0; top: 48px; width: 100%; height: 138px; background: var(--navy); }
  .front-band-accent { position: absolute; left: 0; top: 0; width: 184px; height: 100%; background: var(--gold); }
  .brand-circle {
    position: absolute; left: 120px; top: 50px; width: 130px; height: 130px;
    border-radius: 50%; background: var(--navy); border: 5px solid #c9ccd4;
  }
  .brand-name {
    position: absolute; left: 60px; top: 196px; width: 250px;
    font-size: 19px; font-weight: 500; line-height: 1.25; color: var(--navy);
    text-align: center;
  }
  .contact-block { position: absolute; left: 378px; }
  .person { top: 64px; line-height: 1.3; }
  .person-name { font-size: 27px; font-weight: 500; color: var(--gold); }
  .person-role, .person-phone { font-size: 20px; font-weight: 400; color: var(--white); line-height: 1.6; }
  .address { top: 212px; font-size: 20px; color: var(--ink-soft); line-height: 1.3; }
  .links { top: 280px; list-style: none; font-size: 19px; color: var(--ink); line-height: 1.45; }
  .links li { display: flex; align-items: center; gap: 8px; }
  .links svg { width: 15px; height: 15px; flex: none; }

  /* Back */
  .card-back { top: 637px; }
  .back-field {
    position: absolute; inset: 0;
    background: linear-gradient(180deg, var(--back-top) 0%, #144a90 45%, var(--back-bottom) 100%);
  }
  .back-name {
    position: absolute; left: 0; top: 170px; width: 100%;
    text-align: center; font-size: 40px; font-weight: 400; line-height: 1.25;
    color: var(--white); letter-spacing: 1px;
  }
  .back-url {
    position: absolute; left: 0; top: 348px; width: 100%;
    text-align: center; font-size: 21px; letter-spacing: 3px; color: var(--white);
  }
</style>
</head>
<body>
<main class="canvas">

  <section class="card card-front" aria-label="Business card front">
    <div class="front-band"><div class="front-band-accent"></div></div>
    <div class="brand-circle"></div>
    <p class="brand-name">Corvane Motion Limited</p>

    <div class="contact-block person">
      <p class="person-name">Owen Pritchard</p>
      <p class="person-role">Managing Director</p>
      <p class="person-phone">+44 (0)7582 913 406</p>
    </div>

    <address class="contact-block address">
      2913 Willowmere Lane<br>Pontcanna, Cardiff CF11 9QT
    </address>

    <ul class="contact-block links">
      <li>
        <svg viewBox="0 0 16 16" aria-hidden="true"><rect x="1" y="3" width="14" height="10" fill="#2b2f4a"/><path d="M1 3l7 6 7-6" fill="none" stroke="#f1f1f1" stroke-width="1.3"/></svg>
        sales@corvanemotion.co.uk
      </li>
      <li>
        <svg viewBox="0 0 16 16" aria-hidden="true"><circle cx="8" cy="8" r="7" fill="#2b2f4a"/><path d="M1 8h14M8 1c-3 3-3 11 0 14M8 1c3 3 3 11 0 14" fill="none" stroke="#f1f1f1" stroke-width="1"/></svg>
        Corvanemotion.co.uk
      </li>
      <li>
        <svg viewBox="0 0 16 16" aria-hidden="true"><rect x="1" y="1" width="14" height="14" rx="2" fill="#2b2f4a"/></svg>
        @motionLetterbin
      </li>
      <li>
        <svg viewBox="0 0 16 16" aria-hidden="true"><rect x="1" y="1" width="14" height="14" rx="1" fill="#2b2f4a"/></svg>
        Corvane Motion Limited
      </li>
    </ul>
  </section>

  <section class="card card-back" aria-label="Business card back">
    <div class="back-field" role="img" aria-label="Faint world map over a deep blue gradient"></div>
    <p class="back-name">Corvane Motion Limited</p>
    <p class="back-url">www.Corvanemotion.co.uk</p>
  </section>

</main>
</body>
</html>
```